Verdo Consultants Exhibition Booth Design. Cannabis Legal Consultancy

We require a design for the following artwork in PDF of Jpeg high resolution format with these specifications, a 5cm bleed outside and a 10cm safe inside bleed. A tension fabric backdrop 200cm wide and 231cm high. (example loaded) Please see our website www.theverdoconsultants.co.uk
Attached are company logos and head shots for inclusion. You will see our colour schemes from the website. It should announce who we are and provide the company website.

```html
<!DOCTYPE html>
<html lang="en">
<head>
<meta charset="utf-8">
<title>Verdo Consultants – Who We Are Backdrop</title>
<link rel="stylesheet" href="https://fonts.googleapis.com/css2?family=Abel&family=Montserrat:wght@400;500;800&display=swap">
<style>
  :root {
    --page: #ffffff;
    --leaf-dark: #07140a;
    --leaf-mid: #143a1c;
    --leaf-light: #1f5a2a;
    --frame-green: #35c24c;
    --box-line: #5d7a60;
    --text: #ffffff;
    --photo-grey: #c9cbcc;
    --photo-grey-light: #dcdcdd;
    --photo-suit: #2a2f3f;
    --photo-navy: #1e2640;
  }
  * { box-sizing: border-box; margin: 0; padding: 0; }
  html, body {
    width: 1157px; height: 1200px; overflow: hidden;
    background: var(--page);
  }
  .backdrop {
    position: absolute; left: 127px; top: 80px;
    width: 899px; height: 1038px;
    overflow: hidden;
    color: var(--text);
    font-family: "Montserrat", sans-serif;
  }
  .foliage {
    position: absolute; inset: 0;
    background:
      radial-gradient(ellipse at 20% 30%, var(--leaf-light) 0%, transparent 45%),
      radial-gradient(ellipse at 80% 75%, var(--leaf-light) 0%, transparent 45%),
      radial-gradient(ellipse at 60% 15%, var(--leaf-mid) 0%, transparent 50%),
      linear-gradient(160deg, var(--leaf-mid), var(--leaf-dark) 60%, var(--leaf-mid));
  }
  .outer-frame {
    position: absolute; left: 9px; top: 16px; right: 9px; bottom: 16px;
    border: 5px solid var(--frame-green);
  }
  .brand-name {
    position: absolute; left: 0; right: 0; top: 58px;
    text-align: center;
    font-weight: 500; font-size: 30px; line-height: 36px;
    letter-spacing: 0.5px;
  }
  .brand-web {
    position: absolute; left: 0; right: 0; top: 100px;
    text-align: center;
    font-weight: 400; font-size: 12px; line-height: 14px;
  }
  .headshot {
    position: absolute; top: 176px; width: 361px; height: 310px;
    border: 4px solid var(--text);
  }
  .headshot--left {
    left: 75px;
    background: linear-gradient(180deg, var(--photo-grey) 0%, var(--photo-grey) 55%, var(--photo-suit) 100%);
  }
  .headshot--right {
    left: 463px;
    background: linear-gradient(180deg, var(--photo-grey-light) 0%, var(--photo-grey-light) 55%, var(--photo-navy) 100%);
  }
  .about {
    position: absolute; left: 71px; top: 527px; width: 759px; height: 397px;
    border: 3px solid var(--box-line);
    background: rgba(0, 0, 0, 0.25);
  }
  .about-title {
    position: absolute; left: 0; right: 0; top: 22px;
    text-align: center; font-weight: 800; font-size: 54px; line-height: 60px;
    letter-spacing: 0.5px;
  }
  .about-rule {
    position: absolute; left: 297px; top: 94px; width: 160px; height: 3px;
    background: var(--text);
  }
  .about-text {
    position: absolute; left: 46px; top: 106px; width: 664px;
    font-size: 21px; line-height: 30px; font-weight: 400;
    text-align: justify; text-align-last: center;
  }
  .site-url {
    position: absolute; left: 0; right: 0; top: 961px;
    text-align: center; font-family: "Abel", sans-serif;
    font-size: 40px; line-height: 44px;
  }
</style>
</head>
<body>
  <main class="backdrop">
    <div class="foliage" role="img" aria-label="Background of dense green cannabis leaves"></div>
    <div class="outer-frame"></div>

    <header>
      <p class="brand-name">Verdo Consultants</p>
      <p class="brand-web">www.theverdoconsultants.co.uk</p>
    </header>

    <div class="headshot headshot--left" role="img" aria-label="Headshot of a bearded consultant in a pinstripe suit"></div>
    <div class="headshot headshot--right" role="img" aria-label="Headshot of a consultant in a navy blazer"></div>

    <section class="about">
      <h1 class="about-title">WHO WE ARE</h1>
      <div class="about-rule"></div>
      <p class="about-text">We can undertake and facilitate a top to bottom, seed to shelf, inception to sale assessment of your whole enterprise. We can facilitate a written expert legal opinion as to the compliance of your business and provide guidance on your structure and protection. We can assist you with the implementation of any necessary steps to achieve compliance, including the introduction to our cross-business contacts to make you stronger and more effective in the marketplace.</p>
    </section>

    <p class="site-url">www.theverdoconsultants.co.uk</p>
  </main>
</body>
</html>
```